Non fiction leadership Book Cover design needed for “Stay Bold: Build On Lasting Discipline”

I need a front cover design for a new book 6 X 9 traditional non-fiction book.

Title: "Stay BOLD - Build On Lasting Discipline"

The subtitle is not finalized- so use 2 lines of smaller dummy text

My brand guide is attached (please use the tan color sparingly)

I'd like to see BOLD look like it is in motion and "flying" across the page

Need CREATIVE designs and options

Do not want my picture on the front cover - I do want it on the back cover.

On the front cover I’d like to see creative use of font to create movement on “BOLD”

Target Market(s)

Business leaders

Industry/Entity Type

Aviation

Font styles to use
Other font styles liked:
• See style guide- can add additional font (modern script or san serif)

Colors
0054AA
0677BA
7BADD7
CADEEF
E8F1F8
EB3D1F
EC4F4E
F09395
F8D3D4
FCEDEE

Requirements
Must have
• Creative font use, using perspective to create movement/motion on BOLD
Should not have
• My picture on the front cover- my picture should be on the back cover

```html
<!DOCTYPE html>
<html lang="en">
<head>
<meta charset="utf-8">
<title>Stay Bold: Build On Lasting Discipline</title>
<link rel="stylesheet" href="https://fonts.googleapis.com/css2?family=Anton&family=Bebas+Neue&family=Montserrat:wght@300;400;600&display=swap">
<style>
  :root {
    --page-bg: #d9d9d9;
    --cover-navy: #061046;
    --title-red: #e8202a;
    --author-red: #e3232c;
    --tan-light: #ebc193;
    --tan-mid: #c98b4f;
    --tan-edge: #8a4a14;
    --text-white: #ffffff;
    --placeholder-navy: #0c1858;
  }
  * { box-sizing: border-box; margin: 0; padding: 0; }
  html, body {
    width: 1200px; height: 1200px; overflow: hidden;
    background: var(--page-bg);
  }
  .book-cover {
    position: absolute;
    left: 230px; top: 45px;
    width: 740px; height: 1110px;
    background: var(--cover-navy);
    overflow: hidden;
  }
  .cover-tagline {
    position: absolute; top: 44px; left: 0; width: 100%;
    text-align: center;
    font-family: "Montserrat", sans-serif; font-weight: 400;
    font-size: 15px; line-height: 26px; letter-spacing: 1px;
    color: var(--text-white);
  }
  .title-lead {
    position: absolute; top: 186px; left: 0; width: 100%;
    text-align: center;
    font-family: "Anton", sans-serif;
    font-size: 118px; line-height: 1; letter-spacing: -2px;
    color: var(--title-red);
    transform: scaleX(0.82);
  }
  .title-word {
    position: absolute; left: 74px; top: 317px;
    width: 520px; height: 511px;
    overflow: visible;
  }
  .aircraft-placeholder {
    position: absolute; left: 330px; top: 314px;
    width: 300px; height: 490px;
    border-radius: 150px 150px 40px 40px;
    background: var(--placeholder-navy);
    opacity: 0.9;
  }
  .title-expansion {
    position: absolute; top: 838px; left: 0; width: 100%;
    text-align: center;
    font-family: "Montserrat", sans-serif; font-weight: 300;
    font-size: 27px; letter-spacing: 3.5px;
    color: var(--text-white);
  }
  .author-name {
    position: absolute; top: 990px; left: 0; width: 100%;
    text-align: center;
    font-family: "Montserrat", sans-serif; font-weight: 600;
    font-size: 40px; letter-spacing: -0.5px;
    color: var(--author-red);
  }
</style>
</head>
<body>
  <main class="book-cover">
    <p class="cover-tagline">Lorem ipsum dolor sit amet, consectetuer adipiscing<br>sed diam nonummy nibh euismod tincidunt</p>
    <h1 class="title-lead">STAY</h1>
    <svg class="title-word" viewBox="0 0 520 511" aria-label="BOLD">
      <defs>
        <linearGradient id="tan-metal" x1="0" y1="0" x2="0" y2="1">
          <stop offset="0" stop-color="#e4b88c"/>
          <stop offset="0.25" stop-color="var(--tan-mid)"/>
          <stop offset="0.6" stop-color="#d9a46e"/>
          <stop offset="1" stop-color="var(--tan-light)"/>
        </linearGradient>
      </defs>
      <text x="0" y="511" font-family="'Bebas Neue', sans-serif" font-size="730"
            textLength="520" lengthAdjust="spacingAndGlyphs"
            fill="url(#tan-metal)" stroke="var(--tan-edge)" stroke-width="4">BOLD</text>
    </svg>
    <div class="aircraft-placeholder" role="img" aria-label="Top-down silhouette of a helicopter with crossed rotor blades"></div>
    <p class="title-expansion">BUILD ON LASTING DISCIPLINE</p>
    <p class="author-name">Renata Hollister</p>
  </main>
</body>
</html>
```